Print on top the name of the company: (Or Similar)
Lumora Cleaning & Disinfecting
Because your standards aren't standard.

We adhere to ALL QRV guidelines for both residential and commercial cleaning.

Infection Control is our ultimate goal.

Instructions:
Opening a residential and commercial cleaning and disinfecting company in south Florida.

Targeting high-end residential clients, commercial and healthcare facilities, specializing in Ambulatory Care Guidelines. With a concentration and expertise in targeting Covid 19 and other transmissible pathogens.

WELM trained.
Owned and operated by a licensed BSN Registered Nurse specially ​trained in Infection Control Prevention with over 25 years experience. Over two decades in Ambulatory Surgery Center Administration, Director of Nursing and Infection Control Prevention ad Consulting.

Looking to create a business flier that emphasizes Cleaning & Disinfection
along with the standard expectation for residential and Commercial cleaning services

Target Market(s)

Residential & Commercial

Font styles to use
Decorative

Requirements
Must have
• A checklist for cleaning services

```html
<!DOCTYPE html>
<html lang="en">
<head>
<meta charset="utf-8">
<title>Lumora Cleaning &amp; Disinfecting — Flyer</title>
<link rel="stylesheet" href="https://fonts.googleapis.com/css2?family=Montserrat:wght@400;600;700;800&family=Lato:wght@700;900&display=swap">
<style>
  :root{
    --green:#8dab2e;
    --green-light:#a3c23f;
    --green-dark:#7a9922;
    --headline-green:#7b9a1f;
    --yellow:#f6da08;
    --ink:#161616;
    --text:#2a2a2a;
    --white:#ffffff;
    --page:#ebe8e3;
  }
  *{box-sizing:border-box;margin:0;padding:0}
  html,body{width:1200px;height:1200px;overflow:hidden;background:var(--page)}
  .canvas{position:relative;width:1200px;height:1200px;overflow:hidden}
  .flyer{
    position:absolute;left:157px;top:31px;
    width:1265px;height:1625px;
    transform:scale(.7);transform-origin:0 0;
    background:var(--white);overflow:hidden;
    box-shadow:0 10px 30px rgba(0,0,0,.18);
    font-family:'Montserrat',sans-serif;
  }
  .hero-photo{
    position:absolute;left:0;top:0;width:1265px;height:640px;
    background:linear-gradient(90deg,#f4f5f7 0%,#eef1f5 45%,#dfe7f0 75%,#d6e1ec 100%);
  }
  .product-photo{
    position:absolute;left:800px;top:400px;width:370px;height:312px;
    border-radius:40px 40px 60px 60px;
    background:linear-gradient(160deg,#f1f1f1 0%,#e3e4e6 50%,#4d7fd8 100%);
    opacity:.85;
  }
  .waves{position:absolute;left:0;top:0;width:1265px;height:1625px}
  .headline{
    position:absolute;left:36px;top:118px;
    font-family:'Montserrat',sans-serif;font-weight:800;
    font-size:80px;line-height:80px;letter-spacing:.5px;
    color:var(--headline-green);text-transform:uppercase;
  }
  .tagline{
    position:absolute;left:36px;top:365px;
    font-family:'Lato',sans-serif;font-weight:900;
    font-size:47px;line-height:48px;color:var(--ink);
  }
  .credential{
    position:absolute;left:0;top:668px;width:1265px;text-align:center;
    font-weight:700;font-size:32px;color:var(--white);
    padding-right:0;
  }
  .credential-title{position:relative;display:inline-block;margin-left:0;transform:translateX(2px)}
  .credential-title::after{
    content:"";position:absolute;left:50%;bottom:-14px;width:46px;height:5px;
    margin-left:-23px;background:var(--yellow);
  }
  .credential-text{
    position:absolute;left:60px;top:730px;width:1145px;
    text-align:center;font-size:22.5px;line-height:29px;
    color:var(--white);font-weight:400;
  }
  .brand-label{
    position:absolute;left:371px;top:887px;width:522px;height:117px;
    background:var(--yellow);border-radius:8px 8px 34px 34px;
    display:flex;align-items:center;justify-content:center;
    font-weight:800;font-size:42px;color:var(--ink);letter-spacing:.3px;
  }
  .service-column{position:absolute;top:1043px}
  .service-column.commercial{left:86px}
  .service-column.residential{left:730px}
  .service-icon{
    position:absolute;left:0;top:0;width:82px;height:82px;border-radius:50%;
    background:var(--yellow);display:flex;align-items:center;justify-content:center;
  }
  .service-heading{
    position:absolute;left:97px;top:20px;white-space:nowrap;
    font-family:'Lato',sans-serif;font-weight:700;font-size:32px;color:var(--green);
  }
  .checklist{position:absolute;left:96px;top:78px;list-style:none;width:420px}
  .checklist li{
    display:flex;align-items:center;height:36px;
    font-size:23.5px;color:var(--text);white-space:nowrap;
  }
  .checklist svg{width:21px;height:21px;margin-right:15px;flex:none}
  .divider{position:absolute;left:631px;top:1057px;width:3px;height:350px;background:var(--green)}
  .footer-band{position:absolute;left:0;top:1475px;width:1265px;height:150px;background:var(--green-light)}
  .offer-pill{
    position:absolute;left:154px;top:1450px;width:956px;height:56px;
    background:var(--yellow);border-radius:28px;
    display:flex;align-items:center;justify-content:center;
    font-family:'Lato',sans-serif;font-weight:900;font-size:33px;color:var(--ink);
  }
  .phone{
    position:absolute;left:0;top:1515px;width:1265px;
    display:flex;align-items:center;justify-content:center;gap:18px;
    font-weight:700;font-size:68px;color:var(--white);letter-spacing:1px;
  }
  .phone svg{width:40px;height:64px}
</style>
</head>
<body>
<div class="canvas">
  <article class="flyer">
    <div class="hero-photo" role="img" aria-label="Photo of a worker in a white protective suit and respirator disinfecting a door handle in a bright corridor"></div>

    <svg class="waves" viewBox="0 0 1265 1625" aria-hidden="true">
      <defs>
        <linearGradient id="bandGrad" x1="0" y1="0" x2="1" y2="0">
          <stop offset="0" stop-color="#84a126"/>
          <stop offset=".5" stop-color="#a4c340"/>
          <stop offset="1" stop-color="#8aa82c"/>
        </linearGradient>
      </defs>
      <path d="M0,512 C250,592 520,618 890,622" fill="none" stroke="#f6da08" stroke-width="14"/>
      <path d="M0,545 C300,640 800,640 1265,540 L1265,1022 C1000,900 600,860 0,955 Z" fill="url(#bandGrad)"/>
      <path d="M150,918 C500,828 900,838 1265,948 L1265,1022 C1000,900 600,860 150,918 Z" fill="#7a9922"/>
      <path d="M150,918 C500,828 900,838 1265,948" fill="none" stroke="#ffffff" stroke-width="6"/>
    </svg>

    <div class="product-photo" role="img" aria-label="Photo of spray bottles, a sponge and blue rubber gloves"></div>

    <h1 class="headline">Lumora<br>Cleaning &amp;<br>Disinfecting</h1>
    <p class="tagline">Because your standards<br>aren't standard.</p>

    <div class="credential"><span class="credential-title">WELM trained.</span></div>
    <p class="credential-text">Owned and operated by a licensed BSN Registered Nurse specially trained in Infection Control Prevention with over 25 years experience. Over two decades in Ambulatory Surgery Center Administration, Director of Nursing and Infection Control Prevention ad Consulting.</p>

    <div class="brand-label">Glimmerwell Cleaning</div>

    <section class="service-column commercial">
      <div class="service-icon">
        <svg width="40" height="42" viewBox="0 0 40 42" aria-hidden="true" fill="none" stroke="#161616" stroke-width="2">
          <rect x="12" y="4" width="18" height="34"/>
          <line x1="16" y1="10" x2="16" y2="34"/><line x1="21" y1="10" x2="21" y2="34"/><line x1="26" y1="10" x2="26" y2="34"/>
          <rect x="5" y="24" width="7" height="14"/>
          <line x1="2" y1="38" x2="38" y2="38"/>
        </svg>
      </div>
      <h2 class="service-heading">COMMERCIAL</h2>
      <ul class="checklist">
        <li><svg viewBox="0 0 20 20"><circle cx="10" cy="10" r="8.5" fill="none" stroke="#8dab2e" stroke-width="1.6"/><path d="M6 10.2l2.7 2.7L14 7.5" fill="none" stroke="#8dab2e" stroke-width="1.8"/></svg>Janitorial</li>
        <li><svg viewBox="0 0 20 20"><circle cx="10" cy="10" r="8.5" fill="none" stroke="#8dab2e" stroke-width="1.6"/><path d="M6 10.2l2.7 2.7L14 7.5" fill="none" stroke="#8dab2e" stroke-width="1.8"/></svg>Offices</li>
        <li><svg viewBox="0 0 20 20"><circle cx="10" cy="10" r="8.5" fill="none" stroke="#8dab2e" stroke-width="1.6"/><path d="M6 10.2l2.7 2.7L14 7.5" fill="none" stroke="#8dab2e" stroke-width="1.8"/></svg>Floor maintenance</li>
        <li><svg viewBox="0 0 20 20"><circle cx="10" cy="10" r="8.5" fill="none" stroke="#8dab2e" stroke-width="1.6"/><path d="M6 10.2l2.7 2.7L14 7.5" fill="none" stroke="#8dab2e" stroke-width="1.8"/></svg>Carpet cleaning</li>
        <li><svg viewBox="0 0 20 20"><circle cx="10" cy="10" r="8.5" fill="none" stroke="#8dab2e" stroke-width="1.6"/><path d="M6 10.2l2.7 2.7L14 7.5" fill="none" stroke="#8dab2e" stroke-width="1.8"/></svg>Move-ing</li>
        <li><svg viewBox="0 0 20 20"><circle cx="10" cy="10" r="8.5" fill="none" stroke="#8dab2e" stroke-width="1.6"/><path d="M6 10.2l2.7 2.7L14 7.5" fill="none" stroke="#8dab2e" stroke-width="1.8"/></svg>Move-outs</li>
        <li><svg viewBox="0 0 20 20"><circle cx="10" cy="10" r="8.5" fill="none" stroke="#8dab2e" stroke-width="1.6"/><path d="M6 10.2l2.7 2.7L14 7.5" fill="none" stroke="#8dab2e" stroke-width="1.8"/></svg>Constructions clean-ups</li>
        <li><svg viewBox="0 0 20 20"><circle cx="10" cy="10" r="8.5" fill="none" stroke="#8dab2e" stroke-width="1.6"/><path d="M6 10.2l2.7 2.7L14 7.5" fill="none" stroke="#8dab2e" stroke-width="1.8"/></svg>Estate clean-outs</li>
      </ul>
    </section>

    <div class="divider"></div>

    <section class="service-column residential">
      <div class="service-icon">
        <svg width="42" height="40" viewBox="0 0 42 40" aria-hidden="true">
          <path d="M21 3L3 16h5v20h26V16h5z" fill="#161616"/>
          <rect x="12" y="19" width="5" height="5" fill="#f6da08"/><rect x="25" y="19" width="5" height="5" fill="#f6da08"/>
          <rect x="12" y="27" width="5" height="5" fill="#f6da08"/><rect x="25" y="27" width="5" height="5" fill="#f6da08"/>
          <rect x="18.5" y="26" width="5" height="10" fill="#f6da08"/>
        </svg>
      </div>
      <h2 class="service-heading">RESIDENTIAL</h2>
      <ul class="checklist">
        <li><svg viewBox="0 0 20 20"><circle cx="10" cy="10" r="8.5" fill="none" stroke="#8dab2e" stroke-width="1.6"/><path d="M6 10.2l2.7 2.7L14 7.5" fill="none" stroke="#8dab2e" stroke-width="1.8"/></svg>House cleaning</li>
        <li><svg viewBox="0 0 20 20"><circle cx="10" cy="10" r="8.5" fill="none" stroke="#8dab2e" stroke-width="1.6"/><path d="M6 10.2l2.7 2.7L14 7.5" fill="none" stroke="#8dab2e" stroke-width="1.8"/></svg>Before and after party</li>
        <li><svg viewBox="0 0 20 20"><circle cx="10" cy="10" r="8.5" fill="none" stroke="#8dab2e" stroke-width="1.6"/><path d="M6 10.2l2.7 2.7L14 7.5" fill="none" stroke="#8dab2e" stroke-width="1.8"/></svg>Move-ins</li>
        <li><svg viewBox="0 0 20 20"><circle cx="10" cy="10" r="8.5" fill="none" stroke="#8dab2e" stroke-width="1.6"/><path d="M6 10.2l2.7 2.7L14 7.5" fill="none" stroke="#8dab2e" stroke-width="1.8"/></svg>Move-outs</li>
        <li><svg viewBox="0 0 20 20"><circle cx="10" cy="10" r="8.5" fill="none" stroke="#8dab2e" stroke-width="1.6"/><path d="M6 10.2l2.7 2.7L14 7.5" fill="none" stroke="#8dab2e" stroke-width="1.8"/></svg>Holiday cleaninng</li>
        <li><svg viewBox="0 0 20 20"><circle cx="10" cy="10" r="8.5" fill="none" stroke="#8dab2e" stroke-width="1.6"/><path d="M6 10.2l2.7 2.7L14 7.5" fill="none" stroke="#8dab2e" stroke-width="1.8"/></svg>Seasonal cleaning</li>
        <li><svg viewBox="0 0 20 20"><circle cx="10" cy="10" r="8.5" fill="none" stroke="#8dab2e" stroke-width="1.6"/><path d="M6 10.2l2.7 2.7L14 7.5" fill="none" stroke="#8dab2e" stroke-width="1.8"/></svg>Carper cleaning</li>
        <li><svg viewBox="0 0 20 20"><circle cx="10" cy="10" r="8.5" fill="none" stroke="#8dab2e" stroke-width="1.6"/><path d="M6 10.2l2.7 2.7L14 7.5" fill="none" stroke="#8dab2e" stroke-width="1.8"/></svg>Deodorizing and sanitizing</li>
      </ul>
    </section>

    <div class="footer-band"></div>
    <div class="offer-pill">Call us to find out how you can save money this month!</div>
    <div class="phone">
      <svg viewBox="0 0 40 64" aria-hidden="true"><path d="M14 4c-9 6-12 20-10 32s8 22 17 26l8-10c1-2 0-3-1-4l-7-4c-2-1-3 0-4 1l-2 3c-4-5-5-14-4-21l3 1c2 1 3 0 3-2l1-8c0-2-1-3-3-3z" fill="#f6da08"/></svg>
      <span>(415) 555-01-89</span>
    </div>
  </article>
</div>
</body>
</html>
```